Kestrelway Financial Plans

I am looking for a complete resdesign of my small financial presentation. This is a Word Doc/PDF that I print off when meeting with people in private. I often present my "two pager" that I have been using for years and years. It tells them the basics of what I do, how I help people and foundational financial principles.

I have recently gone out on my own in business and have completely rebranded. This presentation is my most used tool, so it is the first of many things I would like to redo. I am hoping it will somehow coordinate with the colors of my business, not necessarily the EXACT same 3 colors everywhere, but have the design colors compliment.

I've uploaded all my logo designs, as well as the current "two-pager". I am not against it going to 3 pages if needed. As it will still land on 2 pages with duplex printing.

It has always been VERY simple. I am wanting it built into a more professional and design specific format, to show off my branding, without being over cluttered.

I am completely open to ANY graphics changes. Obviously some are very novice, the house on the last page has always been overly simplified.

```html
<!DOCTYPE html>
<html lang="en">
<head>
<meta charset="utf-8">
<title>Kestrelway Financial Plans – Two Pager</title>
<link href="https://fonts.googleapis.com/css2?family=Montserrat:wght@400;500;600;700;800&display=swap" rel="stylesheet">
<style>
:root{
  --navy:#0f2236;
  --green:#1bb14c;
  --green-soft:#bdf5cf;
  --paper:#ffffff;
  --panel:#f2f2f2;
  --stage:#eeeeee;
  --grey:#8c9196;
  --grey-light:#cfd2d5;
  --grey-mid:#b6bbc0;
  --red:#e8141b;
  --ink:#1c1c1c;
}
*{box-sizing:border-box;margin:0;padding:0}
html,body{width:1200px;height:2401px;overflow:hidden}
body{position:relative;background:var(--stage);font-family:'Montserrat',sans-serif;color:var(--ink)}
.abs{position:absolute}
.page{position:absolute;left:219px;width:762px;background:var(--paper);overflow:hidden}
.page-one{top:68px;height:1100px}
.page-two{top:1230px;height:1102px}
.side-panel{position:absolute;left:0;top:0;width:293px;height:100%;background:var(--panel)}
.top-panel{position:absolute;left:0;top:0;width:100%;height:460px;background:var(--panel)}
.pattern{position:absolute;right:0;top:0;width:180px;height:140px}
.footer-band{position:absolute;left:165px;right:0;bottom:0;height:36px;background:linear-gradient(90deg,var(--navy) 0%,var(--navy) 55%,#145a36 85%,var(--green) 100%);color:#fff;font-size:11px;font-weight:500;display:flex;align-items:center;justify-content:flex-end;padding-right:20px;gap:12px;letter-spacing:.2px}
.page-num{width:20px;height:20px;border:1.5px solid #fff;border-radius:50%;display:flex;align-items:center;justify-content:center;font-size:10px}
.corner-mark{position:absolute;left:-30px;bottom:-40px;width:150px;height:110px;border-radius:50%;background:var(--grey-light)}
.brand{left:271px;font-weight:700;color:var(--navy);font-size:21px;letter-spacing:-.3px;line-height:1}
.brand small{display:block;font-size:8px;letter-spacing:2px;margin-top:6px;text-align:center}
.heading{font-weight:800;font-size:26px;line-height:27px;color:var(--navy);letter-spacing:.2px}
.heading .accent{color:var(--green)}
.left-title{font-weight:700;font-size:20px;color:var(--navy)}
.stat{font-size:12.8px;line-height:14.6px;width:218px;color:var(--ink);letter-spacing:-.2px}
.stat b{font-weight:700}
.source{display:inline-block;background:var(--green);color:#fff;font-size:9.5px;font-weight:700;padding:3px 10px;border-radius:9px;margin-top:5px;letter-spacing:0}
.badge{border:1.5px dashed var(--navy);border-radius:50%;display:flex;align-items:center;justify-content:center}
.badge-core{background:var(--navy);border-radius:50%;display:flex;align-items:center;justify-content:center;color:#fff}
.step{text-align:center;color:var(--navy);width:150px}
.step-title{font-weight:800;font-size:15px;line-height:17px}
.step-text{font-size:13.5px;line-height:17px;color:#333;margin-top:8px}
.chev{color:var(--green);font-size:12px;font-weight:800;line-height:12px}
.plan-pill{left:742px;width:196px;height:43px;background:var(--green-soft);display:flex;align-items:center;padding-left:38px;font-size:10px;font-weight:700;color:var(--navy);clip-path:polygon(0 0,93% 0,100% 50%,93% 100%,0 100%)}
.plan-pill::after{content:"";position:absolute;right:0;top:0;width:14px;height:100%;background:var(--green);clip-path:polygon(0 0,50% 0,100% 50%,50% 100%,0 100%,50% 50%)}
.pill-icon{position:absolute;left:12px;top:12px;width:19px;height:19px;border:1.5px solid var(--navy);border-radius:4px}
.arrow-tick{left:724px;color:var(--navy);font-size:14px;font-weight:800}
.partner{width:95px;height:34px;background:#f3f4f5;border-radius:4px;display:flex;align-items:center;justify-content:center}
.partner i{display:block;width:40px;height:10px;border-radius:5px;background:#d9dcdf}
.pay-label{left:535px;width:406px;text-align:center;font-weight:700;font-size:13px;color:var(--navy)}
.rate-head{height:43px;display:flex;font-weight:700;font-size:15px;color:#fff}
.rate-head span{display:flex;align-items:center;justify-content:center}
.rate-head .age{background:var(--navy)}
.rate-head .pct{background:var(--green)}
.rate-row{height:31px;display:flex;align-items:center;font-size:11.5px;border-bottom:1px solid #333}
.rate-row span{text-align:center}
.doubles{text-align:center;font-weight:700;color:var(--navy);font-size:13px;line-height:16px}
.doubles em{display:block;font-style:normal;color:var(--green);font-weight:800;font-size:17px;line-height:17px}
.pillar-cap{height:12px;background:var(--grey-light)}
.pillar-head{height:85px;color:#fff;text-align:center;font-weight:700;font-size:16px;border-radius:8px 8px 0 0;padding-top:10px}
.pillar-head.navy{background:var(--navy)}
.pillar-head.green{background:var(--green)}
.pillar-head .badge{width:42px;height:42px;margin:0 auto 8px;border-color:#fff}
.pillar-body{height:160px;background:#ececec;border-radius:0 0 10px 10px;text-align:center;font-size:11.3px;font-weight:700;color:var(--ink);line-height:15px;padding:18px 10px 0}
.pillar-body p{margin-bottom:9px}
.pillar-tag{height:36px;margin:6px 22px 0;background:#d8d8d8;color:var(--red);font-weight:800;font-size:14px;display:flex;align-items:center;justify-content:center}
.pillar-base{height:8px;margin:3px 12px 0;background:var(--grey-light)}
.foundation{left:302px;top:2178px;width:591px;height:68px;background:var(--grey);border-radius:8px;color:#fff;font-weight:700;font-size:12px;display:flex}
.foundation div{flex:1;display:flex;flex-direction:column;align-items:center;justify-content:center;gap:10px}
.foundation hr{width:200px;border:0;border-top:1px solid #fff}
.placeholder-name{left:818px;top:1740px;font-weight:700;font-size:21px;color:var(--navy)}
</style>
</head>
<body>

<!-- PAGE ONE -->
<section class="page page-one">
  <div class="side-panel"></div>
  <svg class="pattern" role="img" aria-label="Decorative triangle pattern in grey and green" viewBox="0 0 180 140"><defs><linearGradient id="pg1" x1="0" y1="0" x2="1" y2="1"><stop offset="0" stop-color="#e6e8ea"/><stop offset="1" stop-color="#cfeedd"/></linearGradient></defs><polygon points="0,0 180,0 180,140" fill="url(#pg1)"/></svg>
  <div class="corner-mark"></div>
  <div class="footer-band">©KESTRELWAY | FINANCIAL PLANS <span class="page-num">2</span></div>
</section>

<div class="abs brand" style="top:96px">KESTRELWAY<small>FINANCIAL PLANS</small></div>
<h1 class="abs heading" style="left:268px;top:165px">THE FINANCIAL<br><span class="accent">CHALLENGE</span></h1>

<!-- Savings -->
<div class="abs badge" style="left:271px;top:245px;width:44px;height:44px"><div class="badge-core" style="width:36px;height:36px;font-weight:700;font-size:14px">$</div></div>
<div class="abs left-title" style="left:324px;top:255px">SAVINGS</div>
<div class="abs stat" style="left:271px;top:297px">
  <b>49%</b> of canadian employees are living paycheque to paycheque. <b>25%</b> of canadians are unable to cover an unexpected <b>$500</b> expense<br><span class="source">Statline Research (feb 2023)</span>
  <div style="margin-top:12px"><b>25%</b> of canadians need to access their retirement savings early. <b>20%</b> of canadians have no savings. 39% of canadians aged 55-65 have less than <b>$5,000</b> in savings.</div>
  <span class="source">National Policy Office (june 2023)</span>
</div>

<!-- Debt -->
<div class="abs badge" style="left:271px;top:506px;width:44px;height:44px"><div class="badge-core" style="width:36px;height:36px;font-weight:700;font-size:14px">$</div></div>
<div class="abs left-title" style="left:324px;top:517px">DEBT</div>
<div class="abs stat" style="left:271px;top:555px">
  The average canadian has <b>$22,131</b> in consumer debt. Which excludes mortgages.<br><span class="source">Creditrix (aug 2024)</span>
  <div style="margin-top:12px">Over <b>55%</b> of canadians hold credit card debt and the total canadian household debt has increased to <b>$2.52trillion</b>, including consumer credit, mortgage and non-mortgage loans.</div>
  <span class="source">Lenders assoc. (aug 2024)</span>
</div>

<!-- Insurance -->
<div class="abs badge" style="left:272px;top:765px;width:44px;height:44px"><div class="badge-core" style="width:36px;height:36px;font-weight:700;font-size:14px">$</div></div>
<div class="abs left-title" style="left:324px;top:776px">INSURANCE</div>
<div class="abs stat" style="left:273px;top:815px">
  <b>45%</b> of canadians do not have individual life insurance coverage, but <b>48%</b> say their families would face financial trouble within 6 months of losing someone.<br><span class="source">Insurewatch intl. (apr 2023)</span>
  <div style="margin-top:12px">2-in-5 canadians (<b>43%</b> women / <b>44%</b> men) will be diagosed with a form of cancer or other critical illness during their lifetime. Every 7 seconds.</div>
  <span class="source">Wellstat data (june 2024)</span>
</div>

<!-- Facing the challenge -->
<h2 class="abs heading" style="left:535px;top:165px">FACING<br><span class="accent">THE CHALLENGE</span></h2>

<div class="abs badge" style="left:551px;top:244px;width:70px;height:70px"><div class="badge-core" style="width:60px;height:60px;font-size:22px;font-weight:700">$</div></div>
<div class="abs step" style="left:511px;top:318px"><div class="step-title">CASH<br>FLOW</div><div class="step-text">ANALYSZE<br><br><br>FREE UP</div></div>

<div class="abs" style="left:650px;top:232px;font-size:12.5px;line-height:14px;text-align:center">$400<br>$600<div class="chev" style="margin-top:5px">❯</div></div>

<div class="abs badge" style="left:706px;top:244px;width:70px;height:70px"><div class="badge-core" style="width:60px;height:60px"><svg width="28" height="28" viewBox="0 0 28 28" fill="none" stroke="#fff" stroke-width="2"><path d="M3 14a11 9 0 0 1 22 0Z"/><path d="M14 14v8a3 3 0 0 1-6 0"/></svg></div></div>
<div class="abs step" style="left:666px;top:318px"><div class="step-title">CASH FLOW<br>PROTECTION</div><div class="step-text">INCOME<br>PROTECTION</div></div>
<div class="abs" style="left:672px;top:395px;width:140px;font-size:12.5px;line-height:14px;display:flex;justify-content:space-between;text-align:center"><div><div class="chev">⌄</div>Life<br>Insurance</div><div><div class="chev">⌄</div>CI/DI<br>Insurance</div></div>

<div class="abs badge" style="left:850px;top:244px;width:70px;height:70px"><div class="badge-core" style="width:60px;height:60px;font-weight:700;font-size:16px">%</div></div>
<div class="abs step" style="left:810px;top:318px"><div class="step-title">DEBT<br>MANAGEMEN</div><div class="step-text" style="margin-top:4px">20%<div class="chev" style="margin:4px 0">⌄</div>6%-7%</div></div>

<div class="abs badge" style="left:551px;top:452px;width:70px;height:70px"><div class="badge-core" style="width:60px;height:60px;font-weight:800;font-size:20px">+</div></div>
<div class="abs step" style="left:511px;top:527px"><div class="step-title">EMERGENCY<br>FUND</div><div class="step-text">IF/ WHEN<div class="chev" style="margin:5px 0">⌄</div>3/6<br>Months</div></div>

<div class="abs badge" style="left:706px;top:452px;width:70px;height:70px"><div class="badge-core" style="width:60px;height:60px;font-weight:700;font-size:20px">$</div></div>
<div class="abs step" style="left:666px;top:527px"><div class="step-title">BUILD<br>WEALTH</div><div class="step-text">FINANCIAL<br>INDEPENDENCE<br>NUMBER<br>(F.I.N)</div></div>
<div class="abs" style="left:725px;top:645px;width:32px;height:26px;border:2px solid var(--navy);border-radius:4px"></div>

<div class="abs badge" style="left:850px;top:452px;width:70px;height:70px"><div class="badge-core" style="width:60px;height:60px"><svg width="26" height="26" viewBox="0 0 26 26" fill="none" stroke="#fff" stroke-width="2"><rect x="3" y="3" width="20" height="20" rx="2"/><text x="13" y="18" fill="#fff" stroke="none" font-size="12" font-weight="700" text-anchor="middle" font-family="Montserrat,sans-serif">$</text></svg></div></div>
<div class="abs step" style="left:810px;top:527px"><div class="step-title">RESERVE<br>WEALTH</div><div class="step-text">LEAVING<br>A LEGACY<br><br>Will Prep</div></div>

<h2 class="abs heading" style="left:535px;top:704px;font-size:25px">HOW WE WILL DO IT</h2>

<svg class="abs" style="left:530px;top:755px" width="200" height="200" viewBox="530 755 200 200" role="img" aria-label="Pie chart of income: living expenses, taxes, savings, debt">
  <g stroke="#fff" stroke-width="3">
    <path d="M626 850 L626 942 A92 92 0 0 1 626 758 Z" fill="#0f2236"/>
    <path d="M626 850 L626 758 A92 92 0 0 1 713 820 Z" fill="#0f2236"/>
    <path d="M626 850 L713 820 A92 92 0 0 1 713 880 Z" fill="#bdf5cf"/>
    <path d="M626 850 L713 880 A92 92 0 0 1 626 942 Z" fill="#1bb14c"/>
  </g>
  <g font-family="Montserrat,sans-serif" font-weight="700" font-size="11.5" text-anchor="middle">
    <text x="584" y="874" fill="#fff">Living</text><text x="584" y="890" fill="#fff">Expenses</text>
    <text x="653" y="823" fill="#fff">Taxes</text>
    <text x="686" y="856" fill="#0f2236">SAVINGS</text>
    <text x="653" y="921" fill="#fff">Debt</text>
  </g>
</svg>

<div class="abs arrow-tick" style="top:769px">❯</div>
<div class="abs arrow-tick" style="top:818px">❯</div>
<div class="abs arrow-tick" style="top:867px">❯</div>
<div class="abs arrow-tick" style="top:917px">❯</div>
<div class="abs plan-pill" style="top:757px"><span class="pill-icon"></span>RETIREMENT SAVINGS</div>
<div class="abs plan-pill" style="top:807px"><span class="pill-icon"></span>CHILDRREN'S EDUCATION</div>
<div class="abs plan-pill" style="top:857px"><span class="pill-icon"></span>PROPER PROTECTION</div>
<div class="abs plan-pill" style="top:906px"><span class="pill-icon"></span>FREEDOM FROM DEBT</div>

<div class="abs partner" style="left:536px;top:962px"><i></i></div>
<div class="abs partner" style="left:638px;top:962px"><i></i></div>
<div class="abs partner" style="left:741px;top:962px"><i></i></div>
<div class="abs partner" style="left:844px;top:962px"><i></i></div>
<div class="abs partner" style="left:536px;top:1004px"><i></i></div>
<div class="abs partner" style="left:638px;top:1004px"><i></i></div>
<div class="abs partner" style="left:741px;top:1004px"><i></i></div>
<div class="abs partner" style="left:844px;top:1004px"><i></i></div>
<div class="abs partner" style="left:588px;top:1046px"><i></i></div>
<div class="abs partner" style="left:690px;top:1046px"><i></i></div>
<div class="abs partner" style="left:793px;top:1046px"><i></i></div>

<svg class="abs" style="left:534px;top:1086px" width="408" height="14" viewBox="0 0 408 14" fill="none" stroke="#0f2236" stroke-width="1.5"><path d="M1 1v5h198l5 6 5-6h198V1"/></svg>
<div class="abs pay-label" style="top:1104px">PAY US</div>

<!-- PAGE TWO -->
<section class="page page-two">
  <div class="top-panel"></div>
  <svg class="pattern" role="img" aria-label="Decorative triangle pattern in grey and green" viewBox="0 0 180 140"><polygon points="0,0 180,0 180,140" fill="url(#pg1)"/></svg>
  <div class="corner-mark"></div>
  <div class="footer-band">©KESTRELWAY | FINANCIAL PLANS <span class="page-num">2</span></div>
</section>

<div class="abs brand" style="top:1258px">KESTRELWAY<small>FINANCIAL PLANS</small></div>
<h2 class="abs heading" style="left:268px;top:1343px">RULE OF 72</h2>

<div class="abs" style="left:268px;top:1385px;width:162px">
  <div class="rate-head"><span class="age" style="width:83px">AGE</span><span class="pct" style="width:79px">4%</span></div>
  <div class="rate-row"><span style="width:83px;font-weight:700">29</span><span style="width:79px">$10,000</span></div>
  <div class="rate-row"><span style="width:83px;font-weight:700">47</span><span style="width:79px">$20,000</span></div>
  <div class="rate-row"><span style="width:83px;font-weight:700">65</span><span style="width:79px">$40,000</span></div>
</div>
<div class="abs" style="left:430px;top:1385px;width:165px">
  <div class="rate-head" style="margin-left:8px"><span class="age" style="width:78px">AGE</span><span class="pct" style="width:79px">6%</span></div>
  <div class="rate-row"><span style="width:86px;padding-left:8px">29</span><span style="width:79px">$10,000</span></div>
  <div class="rate-row"><span style="width:86px;padding-left:8px">41</span><span style="width:79px">$20,000</span></div>
  <div class="rate-row"><span style="width:86px;padding-left:8px">53</span><span style="width:79px">$40,000</span></div>
  <div class="rate-row"><span style="width:86px;padding-left:8px">65</span><span style="width:79px">$80,000</span></div>
</div>
<div class="abs" style="left:595px;top:1385px;width:165px">
  <div class="rate-head" style="margin-left:9px"><span class="age" style="width:78px">AGE</span><span class="pct" style="width:78px">8%</span></div>
  <div class="rate-row"><span style="width:87px;padding-left:9px">29</span><span style="width:78px">$10,000</span></div>
  <div class="rate-row"><span style="width:87px;padding-left:9px">38</span><span style="width:78px">$20,000</span></div>
  <div class="rate-row"><span style="width:87px;padding-left:9px">47</span><span style="width:78px">$40,000</span></div>
  <div class="rate-row"><span style="width:87px;padding-left:9px">56</span><span style="width:78px">$80,000</span></div>
  <div class="rate-row"><span style="width:87px;padding-left:9px">65</span><span style="width:78px">$160,000</span></div>
</div>
<div class="abs" style="left:760px;top:1385px;width:171px">
  <div class="rate-head" style="margin-left:10px"><span class="age" style="width:80px">AGE</span><span class="pct" style="width:81px">12%</span></div>
  <div class="rate-row"><span style="width:90px;padding-left:10px">29</span><span style="width:81px">$10,000</span></div>
  <div class="rate-row"><span style="width:90px;padding-left:10px">35</span><span style="width:81px">$20,000</span></div>
  <div class="rate-row"><span style="width:90px;padding-left:10px">41</span><span style="width:81px">$40,000</span></div>
  <div class="rate-row"><span style="width:90px;padding-left:10px">47</span><span style="width:81px">$80,000</span></div>
  <div class="rate-row"><span style="width:90px;padding-left:10px">53</span><span style="width:81px">$160,000</span></div>
  <div class="rate-row"><span style="width:90px;padding-left:10px">59</span><span style="width:81px">$320,000</span></div>
</div>

<div class="abs doubles" style="left:268px;top:1628px;width:166px">MONEY DOUBLES<em>EVERY</em><em>18 YEARS</em></div>
<div class="abs doubles" style="left:434px;top:1628px;width:166px">MONEY DOUBLES<em>EVERY</em><em>12 YEARS</em></div>
<div class="abs doubles" style="left:600px;top:1628px;width:166px">MONEY DOUBLES<em>EVERY</em><em>9 YEARS</em></div>
<div class="abs doubles" style="left:765px;top:1628px;width:166px">MONEY DOUBLES<em>EVERY</em><em>6 YEARS</em></div>

<h2 class="abs heading" style="left:268px;top:1717px">STRUCTURE</h2>
<div class="abs placeholder-name">PitchPot</div>

<svg class="abs" style="left:268px;top:1756px" width="664" height="90" viewBox="0 0 664 90">
  <polygon points="60,50 310,2 370,2 620,50" fill="#b6bbc0"/>
  <rect x="0" y="50" width="664" height="12" fill="#cfd2d5"/>
  <rect x="36" y="68" width="592" height="20" fill="#d6d8db"/>
</svg>

<div class="abs" style="left:291px;top:1850px;width:143px">
  <div class="pillar-cap" style="margin:0 12px"></div>
  <div class="pillar-head navy" style="margin-top:13px"><div class="badge"><svg width="20" height="20" viewBox="0 0 20 20" fill="none" stroke="#fff" stroke-width="1.8"><path d="M3 10L10 3l7 7M5 9v8h10V9"/></svg></div>HOME</div>
  <div class="pillar-body"><p>PARTNER WITH MORTGAGE BROKERS FOR BEST RATES</p><p>MORTGAGE INSURANCE ALTERNATIVES</p></div>
  <div class="pillar-tag">SELL</div><div class="pillar-base"></div>
</div>
<div class="abs" style="left:449px;top:1850px;width:142px">
  <div class="pillar-cap" style="margin:0 12px"></div>
  <div class="pillar-head green" style="margin-top:13px"><div class="badge"><span style="font-size:16px">$</span></div>RRSP</div>
  <div class="pillar-body"><p>TAX DEDUCTION</p><p>TAX DEFERRED</p></div>
  <div class="pillar-tag">100% TAX</div><div class="pillar-base"></div>
</div>
<div class="abs" style="left:606px;top:1850px;width:142px">
  <div class="pillar-cap" style="margin:0 12px"></div>
  <div class="pillar-head navy" style="margin-top:13px"><div class="badge"><span style="font-size:16px">$</span></div>TFSA</div>
  <div class="pillar-body"><p>NO TAX DEDUCTIONS</p><p>TAX FREE GROWTH</p><p>2009-$102,000</p><p>2025 LIMIT - $7000/YR</p></div>
  <div class="pillar-tag">0% TAX</div><div class="pillar-base"></div>
</div>
<div class="abs" style="left:764px;top:1850px;width:142px">
  <div class="pillar-cap" style="margin:0 12px"></div>
  <div class="pillar-head green" style="margin-top:13px"><div class="badge"><svg width="20" height="20" viewBox="0 0 20 20" fill="none" stroke="#fff" stroke-width="1.8"><path d="M2 10a8 7 0 0 1 16 0Z"/><path d="M10 10v6"/></svg></div>PERM LIFE</div>
  <div class="pillar-body"><p>NO TAX DEDUCTION</p><p>QUALIFY</p><p>TAX DEFERRED GROWTH</p></div>
  <div class="pillar-tag">0% TAX</div><div class="pillar-base"></div>
</div>

<div class="abs foundation">
  <div>EMERGENCY/OPPORTUNITY FUNDS<hr>CASHFLOW PROTECTION (LI/CI/DI)</div>
  <div>DEBT MANAGEMENT<hr>CASH FLOW</div>
</div>

</body>
</html>
```